Small Business Broker Business Card Design

A business card design for a small business brokerage, which is a financial service, not unlike real estate brokerage, but for small businesses such as laundromats, pizza shops, restaurants, cleaners etc. The designs should all be simple, more conservative in nature, using the colors and font of the logo. Again, think real estate Brokerage as a business context
Contact Information for Business Card
Name: Glen R. Harlow. Title: Small Business Advisor. Email: g.harlow@bayfieldcapitalworks.example. Mobile: (555) 274-3918. Office: (555) 806-2147. www.bayfieldcapitalworks.example

```html
<!DOCTYPE html>
<html lang="en">
<head>
<meta charset="utf-8">
<title>Bayfield Capital Works – Business Card</title>
<link rel="stylesheet" href="https://fonts.googleapis.com/css2?family=Montserrat:wght@300;400;700;800&display=swap">
<style>
  :root {
    --navy: #1b3a6b;
    --navy-light: #22467d;
    --navy-deep: #163159;
    --green: #8cc63f;
    --white: #ffffff;
    --page: #e9ebef;
  }
  * { box-sizing: border-box; margin: 0; padding: 0; }
  html, body { width: 1200px; height: 900px; overflow: hidden; }
  body {
    background: var(--page);
    font-family: "Montserrat", Arial, sans-serif;
    display: flex; flex-direction: column; align-items: center; justify-content: center;
    gap: 36px;
  }
  .card {
    position: relative;
    width: 700px; height: 400px;
    background: var(--navy);
    overflow: hidden;
    box-shadow: 0 6px 18px rgba(0,0,0,.18);
  }
  .card-bands { position: absolute; inset: 0; }
  .brand { display: flex; align-items: center; gap: 14px; }
  .brand-square { width: 26px; height: 26px; background: var(--green); flex: none; }
  .brand-name {
    color: var(--white); font-weight: 800; text-transform: uppercase;
    letter-spacing: .04em; white-space: nowrap;
  }
  .brand-tagline {
    color: var(--green); font-weight: 700; text-transform: uppercase;
    letter-spacing: .12em; white-space: nowrap;
  }

  /* front */
  .card-front .brand-block {
    position: absolute; left: 0; right: 0; top: 150px;
    display: flex; flex-direction: column; align-items: center; gap: 12px;
  }
  .card-front .brand-name { font-size: 30px; }
  .card-front .brand-tagline { font-size: 13px; }

  /* back */
  .card-back .brand-block {
    position: absolute; left: 36px; top: 138px; width: 310px;
    display: flex; flex-direction: column; gap: 7px;
  }
  .card-back .brand { gap: 10px; }
  .card-back .brand-square { width: 16px; height: 16px; }
  .card-back .brand-name { font-size: 14.5px; letter-spacing: .03em; }
  .card-back .brand-tagline { font-size: 6.8px; letter-spacing: .1em; padding-left: 26px; }
  .divider {
    position: absolute; left: 372px; top: 70px; width: 1px; height: 250px;
    background: rgba(255,255,255,.75);
  }
  .contact { position: absolute; left: 402px; top: 74px; color: var(--white); }
  .contact-name {
    color: var(--green); font-weight: 800; font-size: 26px; text-transform: uppercase;
    letter-spacing: .02em; line-height: 1.05;
  }
  .contact-title { font-weight: 400; font-size: 14px; margin-top: 4px; }
  .contact-address { font-weight: 300; font-size: 13px; line-height: 1.45; margin-top: 12px; }
  .contact-list { list-style: none; margin-top: 14px; font-weight: 300; font-size: 12.5px; }
  .contact-list li { display: flex; align-items: center; gap: 9px; line-height: 1.75; }
  .contact-list svg { width: 12px; height: 12px; fill: var(--white); flex: none; }
  .accent-band {
    position: absolute; left: 0; right: 0; bottom: 0; height: 14px; background: var(--green);
  }
</style>
</head>
<body>

  <section class="card card-front" aria-label="Card front">
    <svg class="card-bands" viewBox="0 0 700 400" preserveAspectRatio="none" aria-hidden="true">
      <polygon points="0,60 700,30 700,90 0,125" fill="var(--navy-light)"/>
      <polygon points="0,270 700,240 700,300 0,335" fill="var(--navy-light)"/>
      <polygon points="430,0 560,0 700,180 700,340" fill="var(--navy-deep)" opacity=".6"/>
    </svg>
    <div class="brand-block">
      <div class="brand">
        <span class="brand-square"></span>
        <span class="brand-name">Bayfield Capital Works, Inc</span>
      </div>
      <span class="brand-tagline">Confidently buy or sell a local business today</span>
    </div>
  </section>

  <section class="card card-back" aria-label="Card back">
    <div class="brand-block">
      <div class="brand">
        <span class="brand-square"></span>
        <span class="brand-name">Bayfield Capital Works, Inc</span>
      </div>
      <span class="brand-tagline">Confidently buy or sell a local business today</span>
    </div>

    <span class="divider"></span>

    <div class="contact">
      <h1 class="contact-name">Glen R. Harlow</h1>
      <p class="contact-title">Small Business Advisor</p>
      <p class="contact-address">P.O. Box 214 Harbor Lane<br>Fairview AB, T0H 1L0</p>
      <ul class="contact-list">
        <li>
          <svg viewBox="0 0 24 24" aria-hidden="true"><path d="M6.6 10.8a15.1 15.1 0 0 0 6.6 6.6l2.2-2.2a1 1 0 0 1 1-.25 11.4 11.4 0 0 0 3.6.57 1 1 0 0 1 1 1V20a1 1 0 0 1-1 1A17 17 0 0 1 3 4a1 1 0 0 1 1-1h3.5a1 1 0 0 1 1 1c0 1.25.2 2.45.57 3.6a1 1 0 0 1-.25 1z"/></svg>
          (555) 274-3918
        </li>
        <li>
          <svg viewBox="0 0 24 24" aria-hidden="true"><path d="M7 1h10a2 2 0 0 1 2 2v18a2 2 0 0 1-2 2H7a2 2 0 0 1-2-2V3a2 2 0 0 1 2-2zm0 3v14h10V4zm5 15.5a1 1 0 1 0 0 2 1 1 0 0 0 0-2z"/></svg>
          (555) 806-2147
        </li>
        <li>
          <svg viewBox="0 0 24 24" aria-hidden="true"><path d="M2 5h20v14H2zm2 2v.5l8 5 8-5V7zm0 2.8V17h16V9.8l-8 5z"/></svg>
          g.harlow@bayfieldcapitalworks.example
        </li>
        <li>
          <svg viewBox="0 0 24 24" aria-hidden="true"><path d="M12 2a10 10 0 1 0 0 20 10 10 0 0 0 0-20zm6.9 6h-2.9a15.6 15.6 0 0 0-1.4-3.6A8 8 0 0 1 18.9 8zM12 4c.8 1.2 1.5 2.5 1.9 4h-3.8c.4-1.5 1.1-2.8 1.9-4zM4.3 14a8 8 0 0 1 0-4h3.4a16 16 0 0 0 0 4zm.8 2h2.9c.3 1.3.8 2.5 1.4 3.6A8 8 0 0 1 5.1 16zM8 8H5.1a8 8 0 0 1 4.3-3.6C8.8 5.5 8.3 6.7 8 8zm4 12c-.8-1.2-1.5-2.5-1.9-4h3.8c-.4 1.5-1.1 2.8-1.9 4zm2.3-6H9.7a14.7 14.7 0 0 1 0-4h4.6a14.7 14.7 0 0 1 0 4zm.3 5.6c.6-1.1 1.1-2.3 1.4-3.6h2.9a8 8 0 0 1-4.3 3.6zm1.7-5.6a16 16 0 0 0 0-4h3.4a8 8 0 0 1 0 4z"/></svg>
          www.bayfieldcapitalworks.example
        </li>
      </ul>
    </div>

    <span class="accent-band"></span>
  </section>

</body>
</html>
```